Start-Up für Training, Coaching & Consulting sucht modernes Webdesign!
Zielgruppe
Wer ist TAVI Training, Coaching & Consulting?
Wir führen Führungskräftetrainings durch, machen Privatkunden für Bewerbungen fit und unterstützen Unternehmen mit Verkaufstrainings. Wir entwickeln Persönlichkeiten im Coaching. Wir beraten Unternehmen und helfen ihnen dabei, ihre Geschäftsabläufe und Prozesse zu optimieren. Dabei steht unsere hohe Qualität im Mittelpunkt - gemeinsam mit unseren kreativen Trainingsmethoden. Unser Background (Diplom-Kaufleute und geprüfte Trainer) bietet dafür die passende Ausgangslage.
Was bedeutet TAVI?
Tavi ist Maori und bdeutet Kreis/Spirale. Er symbolisiert einen wachsenden Silberfarn und steht für persönliche Entwicklung und Entfaltung. Der Tavi ist einerseits unser Namensgeber und unser Logo, andererseits steht der Tavi aber auch für unsere Werte: Denn wir wollen unseren Kunden dabei helfen zu wachsen und sich weiterzuentwickeln - und dies auf eine hochqualitative und seriöse Art und Weise ohne den Eindruck von Esoterik oder Erlebnispädagogik zu vermitteln.
Aufgabenstellung
Modernes Design, das unsere Philosophie widerspiegelt: Wir möchten unseren Kunden auf seriöse und hochqualitative Weise weiterentwickeln. Wir stehen für nachhaltigen Lernerfolg, kreative Trainingsmethoden, Abwechslung, Spaß am Lernen, Qualität, Kompetenz, Fachwissen und Dynamik.
Layout:
1) Header: QMSR geprüfter Trainer, Menüpunkte (siehe Architektur)
2) Banner
3) 3 Teaser (Training, Coaching, Consulting) + Header + 2-3 Zeilen Text (+Icons)
>>> Sichtbarer Bereich auf Homepage: Menü, Banner, Teaser
4) "Warum Sie uns wählen sollten": 5 bullet points ohne weiteren Text
5) "Aus unserem Blog": Frame für 3 Blogartikel + Bild + Datum + Header + 2-3 Zeilen Text
6) Alle drei QMSR Logos
7) Footer: Click Us (quick links), Contact Us (Adresse), Follow Us (Pinnwald, ZOLP, Kontaktor)
8) Copyright + Impressum
>>> Das Design soll klar sein, aber nicht zu kantig. Vielmehr sollen abgerundete Ecken und dynamische Elemente genutzt werden.
Architektur:
3 Ebenen:
1) Homepage
2) TAVI, Training, Coaching, Consulting, für Trainer, Kundenstimmen/Referenzen, Kontakt
3) noch zu bestimmende Produktdetailseiten
Texte werden noch erstellt, Layout kann ggf. mit Platzhaltertext gefüllt werden.
Bildmaterial: Logo und vorhandenes Imagebild werden zur Verfügung gestellt. Bilder können ggf. gekauft werden. Vorschläge erwünscht.
Corporate colors:
grün: #a2c61b + monochromatic colors
http://www.tintoskop.de/a2c61b
grau: #474747 + monochromatic colors
http://www.tintoskop.de/474747

```html
<!DOCTYPE html>
<html lang="de">
<head>
<meta charset="utf-8">
<title>TAVI Training, Coaching &amp; Consulting</title>
<link href="https://fonts.googleapis.com/css2?family=Nunito+Sans:wght@300;400;600;700;800&display=swap" rel="stylesheet">
<style>
:root{
  --green:#a2c61b;
  --green-soft:#d7e89a;
  --grey:#474747;
  --grey-dark:#2b2d2f;
  --grey-light:#e9e9e9;
  --text:#3a3a3a;
  --footer-text:#d4d4d4;
  --footer-head:#c9c9c9;
  --white:#fff;
  --qmsr:#1565b3;
}
*{margin:0;padding:0;box-sizing:border-box}
html,body{width:795px;height:1200px;overflow:hidden;background:var(--white)}
body{font-family:"Nunito Sans",sans-serif;color:var(--text);position:relative}
.abs{position:absolute}

/* header */
.site-header{position:absolute;left:0;top:0;width:795px;height:53px;background:var(--white)}
.brand{position:absolute;left:112px;top:9px}
.brand-name{font-weight:800;font-size:24px;color:var(--grey);letter-spacing:1px;line-height:26px;display:flex;align-items:center;gap:5px}
.brand-dot{width:10px;height:10px;border-radius:50%;background:var(--green)}
.brand-tag{font-size:5px;color:var(--grey);margin-top:3px}
.badge{position:absolute;background:var(--qmsr);border-radius:2px}
.main-nav{position:absolute;left:302px;top:0;height:53px;display:flex;align-items:center;font-size:8.5px;color:var(--grey)}
.main-nav a{color:inherit;text-decoration:none;display:flex;align-items:center;height:53px}
.main-nav .active{background:var(--green);color:var(--white);padding:0 9px}
.main-nav .sep{margin:0 14px;font-size:7px}
.caret{width:6px;height:6px;margin-left:3px}

/* hero */
.hero{position:absolute;left:0;top:53px;width:795px;height:290px}
.hero-title{position:absolute;left:0;top:68px;width:795px;text-align:center;color:var(--white);font-weight:300;font-size:30px;line-height:35px}
.hero-title b{font-weight:800}
.hero-sub{position:absolute;top:135px;width:795px;text-align:center;color:var(--white);font-size:13px;font-weight:400}
.hero-btn{position:absolute;left:347px;top:162px;width:99px;height:33px;border-radius:17px;background:var(--green);color:var(--white);font-size:8px;font-weight:700;display:flex;align-items:center;justify-content:center}
.hero-arrow{position:absolute;top:148px;width:28px;height:44px}

/* teasers */
.teaser{position:absolute;top:370px;width:161px}
.teaser-title{position:absolute;left:0;top:0;width:161px;text-align:center;color:var(--green);font-weight:700;font-size:11.5px;padding-left:20px}
.teaser-card{position:absolute;top:22px;left:0;width:161px;height:136px;border-radius:12px 12px 10px 10px;background:var(--grey-light);box-shadow:0 2px 0 #bdbdbd;overflow:hidden}
.teaser-img{height:86px}
.teaser-text{font-size:6.6px;text-align:center;line-height:10.5px;padding:8px 6px 0}
.teaser-icon{position:absolute;left:-22px;top:-1px;width:44px;height:44px;border-radius:50%;background:var(--green);border:2px solid var(--white);box-shadow:0 0 2px rgba(0,0,0,.2)}

/* dividers */
.divider{position:absolute;left:80px;width:635px;height:1px;background:#d9e5b0}
.divider-mark{position:absolute;left:377px;width:40px;height:32px;background:var(--white)}
.divider-mark span{position:absolute;left:6px;top:2px;width:28px;height:28px;border-radius:50%;background:radial-gradient(circle at 45% 45%,#eef5d0,var(--green-soft) 60%,#c4dc5e)}

/* why */
.section-title{position:absolute;top:621px;font-size:17px;font-weight:400;color:var(--grey-dark)}
.why-list{position:absolute;left:118px;top:663px;list-style:none}
.why-list li{display:flex;align-items:center;height:29.7px;font-size:12.5px;color:var(--grey-dark)}
.why-list svg{width:15px;height:15px;margin-right:8px}

/* blog */
.post{position:absolute;left:457px;width:224px;height:70px;background:var(--grey-light);border-radius:4px;box-shadow:0 2px 0 #bdbdbd}
.post-thumb{position:absolute;left:7px;top:8px;width:59px;height:54px;border-radius:4px}
.post-body{position:absolute;left:74px;top:8px;width:144px;font-size:6.6px;line-height:10.5px;color:var(--grey-dark)}
.post-body strong{font-weight:700;display:block}
.more{position:absolute;right:9px;bottom:6px;width:37px;height:11px;border-radius:6px;background:var(--green);color:var(--white);font-size:6.5px;text-align:center;line-height:11px}

/* footer */
.footer-head{position:absolute;top:1036px;font-weight:400;font-size:8.5px;color:var(--footer-head);letter-spacing:.3px}
.quick-links{position:absolute;left:139px;top:1057px;list-style:none;font-size:8px;line-height:10.6px;color:var(--footer-text)}
.contact{position:absolute;font-size:6px;line-height:8.5px;color:var(--footer-text)}
.contact svg{position:absolute;left:-17px;top:0}
.social{position:absolute;top:1055px;height:21px;padding:0 4px;border-radius:11px;background:var(--green);color:var(--white);font-size:5.5px;font-weight:700;line-height:21px;text-align:center}
.footer-brand{position:absolute;left:575px;top:1053px}
.footer-brand .brand-name{color:var(--white)}
.footer-brand .brand-tag{color:var(--footer-text)}
.dotted{position:absolute;left:118px;top:1134px;width:559px;border-top:1px dotted #8a8f5a}
.legal{position:absolute;top:1141px;width:795px;text-align:center;font-size:8px;line-height:12.5px;color:#b9b9b9}
.legal span{color:var(--green)}
</style>
</head>
<body>

<header class="site-header">
  <div class="brand">
    <div class="brand-name"><span>TAVI</span><span class="brand-dot"></span></div>
    <div class="brand-tag">Training • Coaching • Consulting</div>
  </div>
  <div class="badge" style="left:201px;top:19px;width:66px;height:18px"></div>
  <nav class="main-nav">
    <a class="active">HOME</a><span class="sep">I</span>
    <a>ÜBER UNS<svg class="caret" viewBox="0 0 6 6"><path d="M.5 1.5 3 4l2.5-2.5" stroke="#a2c61b" stroke-width="1.4" fill="none"/></svg></a><span class="sep">I</span>
    <a>FÜR TRAINERS<svg class="caret" viewBox="0 0 6 6"><path d="M.5 1.5 3 4l2.5-2.5" stroke="#a2c61b" stroke-width="1.4" fill="none"/></svg></a><span class="sep">I</span>
    <a>REFERENZEN</a><span class="sep" style="margin:0 18px">I</span>
    <a>KONTAKT</a>
  </nav>
</header>

<section class="hero">
  <svg class="abs" width="795" height="290" viewBox="0 0 795 290" role="img" aria-label="Nahaufnahme sich entrollender Farnwedel in Grün">
    <defs>
      <radialGradient id="fern" cx="50%" cy="45%" r="70%">
        <stop offset="0" stop-color="#5aa032"/><stop offset=".6" stop-color="#37801f"/><stop offset="1" stop-color="#1f5a14"/>
      </radialGradient>
      <linearGradient id="band" x1="0" x2="1">
        <stop offset="0" stop-color="#d5e86b"/><stop offset=".5" stop-color="#a2c61b"/><stop offset="1" stop-color="#c9e04a"/>
      </linearGradient>
    </defs>
    <path d="M0 0H795V155C740 230 640 280 480 275C330 270 200 215 0 230Z" fill="url(#fern)"/>
    <path d="M0 215C120 205 230 235 360 258C500 282 640 280 720 230C760 205 785 180 795 155V172C770 220 700 280 520 283C380 286 250 255 120 236C70 230 30 232 0 236Z" fill="url(#band)"/>
  </svg>
  <svg class="hero-arrow" style="left:48px" viewBox="0 0 28 44"><path d="M24 3 5 22l19 19" stroke="rgba(255,255,255,.75)" stroke-width="6" fill="none"/></svg>
  <svg class="hero-arrow" style="left:719px" viewBox="0 0 28 44"><path d="M4 3l19 19L4 41" stroke="rgba(255,255,255,.75)" stroke-width="6" fill="none"/></svg>
  <h1 class="hero-title">TRAINING, COACHING<br>CONSULTING <b>FÜR TRAINER</b></h1>
  <p class="hero-sub">Lorem ipsum dolor sit amet consectetur adipiscing elit.</p>
  <div class="hero-btn">MEHR ERFAHREN</div>
</section>

<article class="teaser" style="left:114px">
  <h2 class="teaser-title">TRAINING</h2>
  <div class="teaser-card">
    <div class="teaser-img" role="img" aria-label="Turm aus Holzklötzen vor dunklem Hintergrund" style="background:linear-gradient(90deg,#3e3e3e,#5a5a5a 60%,#474747)"></div>
    <p class="teaser-text">Lorem ipsum dolor sit amet, consectetur adipiscing elit. In dapibus accumsan luctus. Lorem ipsum dolor sit adipiscing elit.</p>
  </div>
  <div class="teaser-icon"></div>
</article>
<article class="teaser" style="left:319px">
  <h2 class="teaser-title">COACHING</h2>
  <div class="teaser-card">
    <div class="teaser-img" role="img" aria-label="Hand setzt ein weißes Puzzleteil ein" style="background:linear-gradient(90deg,#ececec,#d9d3cc 55%,#c79a80)"></div>
    <p class="teaser-text">Lorem ipsum dolor sit amet, consectetur adipiscing elit. In dapibus accumsan luctus. Lorem ipsum dolor sit adipiscing elit.</p>
  </div>
  <div class="teaser-icon"></div>
</article>
<article class="teaser" style="left:521px">
  <h2 class="teaser-title">CONSULTING</h2>
  <div class="teaser-card">
    <div class="teaser-img" role="img" aria-label="Altes Holztor mit Vorhängeschloss" style="background:linear-gradient(90deg,#4f4a43,#6b5f52 50%,#3f3a35)"></div>
    <p class="teaser-text">Lorem ipsum dolor sit amet, consectetur adipiscing elit. In dapibus accumsan luctus. Lorem ipsum dolor sit adipiscing elit.</p>
  </div>
  <div class="teaser-icon"></div>
</article>

<div class="divider" style="top:584px"></div>
<div class="divider-mark" style="top:566px"><span role="img" aria-label="Grünes Spiral-Ornament"></span></div>

<svg class="abs" style="left:0;top:770px" width="400" height="90" viewBox="0 0 400 90"><path d="M0 55C140 80 280 95 397 5V40C300 100 150 90 0 65Z" fill="#eef5d6"/></svg>

<h2 class="section-title" style="left:139px">WHY CHOOSE US</h2>
<ul class="why-list">
  <li><svg viewBox="0 0 15 15"><circle cx="7.5" cy="7.5" r="7.5" fill="#a2c61b"/><path d="M6 4.5 9 7.5 6 10.5" stroke="#fff" stroke-width="1.6" fill="none"/></svg>Vestibulum nec mauris facilisis</li>
  <li><svg viewBox="0 0 15 15"><circle cx="7.5" cy="7.5" r="7.5" fill="#a2c61b"/><path d="M6 4.5 9 7.5 6 10.5" stroke="#fff" stroke-width="1.6" fill="none"/></svg>Curabitur et tristique diam, nec sagittis nibh</li>
  <li><svg viewBox="0 0 15 15"><circle cx="7.5" cy="7.5" r="7.5" fill="#a2c61b"/><path d="M6 4.5 9 7.5 6 10.5" stroke="#fff" stroke-width="1.6" fill="none"/></svg>Denim nec sagittis nibh</li>
  <li><svg viewBox="0 0 15 15"><circle cx="7.5" cy="7.5" r="7.5" fill="#a2c61b"/><path d="M6 4.5 9 7.5 6 10.5" stroke="#fff" stroke-width="1.6" fill="none"/></svg>Vestibulum nec mauris facilisis</li>
  <li><svg viewBox="0 0 15 15"><circle cx="7.5" cy="7.5" r="7.5" fill="#a2c61b"/><path d="M6 4.5 9 7.5 6 10.5" stroke="#fff" stroke-width="1.6" fill="none"/></svg>Tristique diam nec lorem</li>
</ul>

<h2 class="section-title" style="left:465px">BLOG</h2>
<article class="post" style="top:655px">
  <div class="post-thumb" role="img" aria-label="Zwei Geschäftsleute mit Tablet im Büro" style="background:linear-gradient(135deg,#cdd6e0,#3d4a5c)"></div>
  <div class="post-body">08.12.2015<strong>LOREM IPSUM DOLOR</strong>Pellentesque habitant morbi tristique senectus et netus et malesuada fames ac turpis egestas.</div>
  <div class="more">more</div>
</article>
<article class="post" style="top:730px">
  <div class="post-thumb" role="img" aria-label="Hände mit Tablet auf einem Schreibtisch" style="background:linear-gradient(135deg,#e4eaf0,#9aa8b5)"></div>
  <div class="post-body">08.12.2015<strong>LOREM IPSUM DOLOR</strong>malesuada fames ac turpis egestas morbi tristique senectus et netus fames ac turpis egestas eto eni.</div>
  <div class="more">more</div>
</article>
<article class="post" style="top:805px">
  <div class="post-thumb" role="img" aria-label="Gefaltete Hände auf einem Konferenztisch" style="background:linear-gradient(180deg,#9fb3c9,#4b5a6a)"></div>
  <div class="post-body">08.12.2015<strong>LOREM IPSUM DOLOR</strong>Gabitant morbi tristique senectus et netus et malesuada fames ac turpis egestas. Lorem ispum dolor.</div>
  <div class="more">more</div>
</article>

<div class="divider" style="top:885px"></div>
<div class="divider-mark" style="top:867px"><span role="img" aria-label="Grünes Spiral-Ornament"></span></div>

<div class="badge" style="left:273px;top:938px;width:66px;height:18px"></div>
<div class="badge" style="left:368px;top:930px;width:24px;height:32px"></div>
<div class="badge" style="left:447px;top:930px;width:24px;height:32px"></div>

<svg class="abs" style="left:0;top:890px" width="795" height="310" viewBox="0 0 795 310">
  <defs><linearGradient id="fband" x1="0" x2="1"><stop offset="0" stop-color="#c9e04a"/><stop offset=".5" stop-color="#a2c61b"/><stop offset="1" stop-color="#b9d62f"/></linearGradient></defs>
  <path d="M0 95C200 95 330 130 470 118C620 105 720 70 795 10V310H0Z" fill="url(#fband)"/>
  <path d="M0 105C200 105 330 140 470 128C620 115 720 80 795 25V310H0Z" fill="#2b2d2f"/>
</svg>

<h4 class="footer-head" style="left:139px">CLICK US</h4>
<ul class="quick-links"><li>Home</li><li>Über uns</li><li>Für trainers</li><li>Referenzen</li><li>Kontakt</li></ul>

<h4 class="footer-head" style="left:249px">CONTACT US</h4>
<div class="contact" style="left:249px;top:1058px">
  <svg width="13" height="11" viewBox="0 0 13 11"><path d="M6.5 0 13 6h-2v5H8V7.5H5V11H2V6H0Z" fill="#a2c61b"/></svg>
  Vestibulum nec mauris 62<br>Suscipit est et<br>62134 Townname
</div>
<div class="contact" style="left:357px;top:1058px">
  <svg width="12" height="12" viewBox="0 0 12 12"><rect width="12" height="12" rx="2" fill="#a2c61b"/><path d="M3.5 2.5c-.8.8 0 3 2 5s4.2 2.8 5 2l-1.5-1.5-1 .6c-.8-.4-1.7-1.3-2.1-2.1l.6-1Z" fill="#2b2d2f"/></svg>
  000 481 2260 517<br>(000 481 2260 517
</div>
<div class="contact" style="left:357px;top:1082px">
  <svg width="13" height="9" viewBox="0 0 13 9"><rect width="13" height="9" rx="1" fill="#a2c61b"/><path d="M0 .5 6.5 5 13 .5" stroke="#2b2d2f" fill="none"/></svg>
  info@tavi-training.de
</div>

<h4 class="footer-head" style="left:476px">FOLLOW US</h4>
<span class="social" style="left:448px;width:35px">Pinnwald</span>
<span class="social" style="left:487px;width:31px">Kurzruf</span>
<span class="social" style="left:522px;width:37px">Kontaktor</span>

<div class="footer-brand">
  <div class="brand-name"><span>TAVI</span><span class="brand-dot"></span></div>
  <div class="brand-tag">Training • Coaching • Consulting</div>
</div>

<div class="dotted"></div>
<p class="legal"><span>Copyright + Impressum</span><br>Aliquam at pulvinar mi. Nulla eget bibendum nisl. Integer consectetur quam ac purus pharetra pulvinar.<br>Aenean faucibus tortor ac tortor aliquet tincidunt. Mauris eget maximus urna.</p>

</body>
</html>
```